A business card design for a dental office. We have Two doctors working here. We practice general de

I already have a logo designed for the office with the name and a slogan.
Now I need to create design for a business card using the same logo.
Details Needed on the front side of the card are :
Bernard K. Oswin, DDS
Gerald M Fenwick, DDS
418 Birch Lane
Portland, CT 00000
Phone : 555 019 4831
Fax : 555 019 4832
Website : WWW.BrightmoorToothHaven.Com
Office hours by appointment
On the back side of the card need :
Appointment
Date....................Time...................
With....................................
If unable to keep your appointment, please give 24-48 hours notice in order to avoid broken appointment fee.

Industry/Entity Type

Dental Clinic

Contact Information for Business Card

Bernard K. Oswin, DDS
Gerald M Fenwick, DDS
418 Birch Lane
Portland, CT 00000
Phone : 555 019 4831
Fax : 555 019 4832
Appointment

Requirements
Must have
• Keep the Name and slogan on the logo on the front of the card. You can move them around the Logo and Name/Slogan of business (Oswin Family Dentistry/We give you reasons to smile) as you wish to get a feel of the design.
• Bernard K. Oswin, DDS
• Gerald M Fenwick, DDS
• 418 Birch Lane
• Portland, CT 00000
• Phone : 555 019 4831
• Fax : 555 019 4832
• WWW.BrightmoorToothHaven.Com
• Keep these three groups above as they are together now in different areas of the front side.
• On the back side of the card need :
• Appointment
• Date....................Time...................
• With....................................
• If unable to keep your appointment, please give 24-48 hours notice in order to avoid broken appointment fee.

```html
<!DOCTYPE html>
<html lang="en">
<head>
<meta charset="utf-8">
<title>Oswin Family Dentistry – Business Card</title>
<link href="https://fonts.googleapis.com/css2?family=Source+Sans+3:wght@400;600;700&display=swap" rel="stylesheet">
<style>
  :root {
    --backdrop: #3a3431;
    --card-dark: #1d1d1f;
    --card-light: #fbfbf9;
    --teal: #1fa58c;
    --white: #f2f2f2;
    --brand-blue: #1f4f9e;
    --alert-red: #e2262b;
    --rule-blue: #2a5fb8;
    --divider: #3d5a55;
  }
  * { box-sizing: border-box; margin: 0; padding: 0; }
  html, body { width: 1200px; height: 844px; overflow: hidden; }
  body {
    background: var(--backdrop);
    font-family: "Source Sans 3", "Myriad Pro", sans-serif;
    position: relative;
  }
  .card {
    position: absolute;
    top: 268px;
    width: 540px;
    height: 308px;
    border-radius: 4px;
    box-shadow: 0 10px 24px rgba(0,0,0,.45);
    overflow: hidden;
  }

  /* Front: contact side */
  .card-front { left: 40px; background: var(--card-dark); }
  .brand-block {
    position: absolute;
    left: 30px; top: 70px;
    width: 200px;
    display: flex; flex-direction: column; align-items: center; gap: 14px;
  }
  .brand-dot {
    width: 110px; height: 110px; border-radius: 50%;
    background: var(--teal);
  }
  .brand-name {
    color: var(--teal);
    font-size: 19px; font-weight: 600;
    text-align: center; line-height: 1.15;
  }
  .contact-divider {
    position: absolute; left: 252px; top: 40px;
    width: 1px; height: 230px; background: var(--divider);
  }
  .contact-block { position: absolute; left: 272px; top: 44px; color: var(--white); }
  .doctor {
    color: var(--teal);
    font-size: 19px; font-weight: 600; line-height: 1.2;
  }
  .address { margin-top: 14px; font-size: 15px; line-height: 1.3; }
  .contact-list { margin-top: 14px; list-style: none; font-size: 15px; line-height: 1.35; }
  .contact-list li { display: flex; align-items: center; gap: 9px; }
  .contact-list svg { width: 12px; height: 12px; fill: var(--teal); flex: none; }
  .hours { margin-top: 4px; font-size: 15px; }

  /* Back: appointment side */
  .card-back { left: 620px; background: var(--card-light); }
  .back-brand {
    position: absolute; left: 28px; top: 26px;
    display: flex; align-items: center; gap: 14px;
  }
  .back-brand .brand-dot { width: 64px; height: 64px; }
  .back-brand .brand-name {
    color: var(--brand-blue); font-size: 19px; font-weight: 700;
    text-transform: uppercase; letter-spacing: .5px; text-align: left;
  }
  .appt-title {
    position: absolute; left: 150px; top: 106px;
    color: var(--alert-red); font-size: 21px; font-weight: 700;
  }
  .appt-field {
    position: absolute;
    display: flex; align-items: flex-end; gap: 8px;
    color: var(--alert-red); font-size: 17px; font-weight: 700;
  }
  .appt-field .line {
    border-bottom: 2px dotted var(--rule-blue);
    height: 1px; margin-bottom: 5px;
  }
  .field-date { left: 30px; top: 150px; }
  .field-date .line { width: 200px; }
  .field-time { left: 300px; top: 150px; }
  .field-time .line { width: 170px; }
  .field-with { left: 30px; top: 196px; }
  .field-with .line { width: 436px; }
  .notice {
    position: absolute; left: 30px; right: 24px; top: 240px;
    font-size: 14.5px; font-weight: 700; line-height: 1.3;
  }
  .notice .first { color: var(--alert-red); display: block; }
  .notice .second { color: var(--brand-blue); display: block; padding-left: 46px; }
</style>
</head>
<body>

  <section class="card card-front" aria-label="Business card front">
    <div class="brand-block">
      <div class="brand-dot"></div>
      <div class="brand-name">Oswin Family Dentistry</div>
    </div>
    <div class="contact-divider"></div>
    <div class="contact-block">
      <p class="doctor">Bernard K. Oswin, DDS</p>
      <p class="doctor">Gerald M Fenwick, DDS</p>
      <p class="address">418 Birch Lane<br>Portland, CT 00000</p>
      <ul class="contact-list">
        <li><svg viewBox="0 0 12 12" aria-label="Phone"><path d="M2.3 0.6l2 2.1-1 1.4c.7 1.6 2 2.9 3.6 3.6l1.4-1 2.1 2-1.3 2.1C4.6 10.5 1.5 7.4.6 2.9z"/></svg>555 019 4831</li>
        <li><svg viewBox="0 0 12 12" aria-label="Fax"><path d="M3 0h6v3H3zM1 4h10v6H9v2H3v-2H1zm3 4v3h4V8z"/></svg>555 019 4832</li>
        <li><svg viewBox="0 0 12 12" aria-label="Website"><circle cx="6" cy="6" r="6"/></svg>WWW.BrightmoorToothHaven.Com</li>
      </ul>
      <p class="hours">Office hours by appointment</p>
    </div>
  </section>

  <section class="card card-back" aria-label="Business card back">
    <div class="back-brand">
      <div class="brand-dot"></div>
      <div class="brand-name">Oswin Family Dentistry</div>
    </div>
    <h2 class="appt-title">Appointment</h2>
    <div class="appt-field field-date"><span>Date</span><span class="line"></span></div>
    <div class="appt-field field-time"><span>Time</span><span class="line"></span></div>
    <div class="appt-field field-with"><span>With</span><span class="line"></span></div>
    <p class="notice">
      <span class="first">If unable to keep your appointment, please give 24-48 hours</span>
      <span class="second">notice in order to avoid broken appointment fee.</span>
    </p>
  </section>

</body>
</html>
```